Cutting Edge Property Services Provider is Looking to Update Business Card Design

We are looking to freshen up our business cards to match our cutting edge technology based image.

KORVANEX - Where Care Finds Its Pulse

More information about our company can be found on our website at www.korvanex-demo.net

We integrate technology in a historically low tech industry.

We have appeared on the Brisk 300/3000 list 2 years in a row and we're previously recognized as the 5th Quickest Rising Firm in San Diego.

Our core colors are blue and white, but are not against accents that might improve our image.

We currently have our Mission Statement on our Business Cards in a folding design:
KORVANEX IS THE LEADING BUILDING SERVICES INNOVATOR. BY COMBINING TECHNOLOGY WITH FUNCTIONAL TOOS THAT IMPROVE EFFICIENCY IN THE WORKPLACE, WE PROVIDE UNPARALLELED SERVICE IN THE INDUSTRY. DEVELOPING LASTING RELATIONSHIPS WITH OUR CLIENTS AND ASSOCIATES IS THE CORNERSTONE OF OUR SUCCESS.

We'd like to convey the image of a cutting edge, technology based company. Want the cards to pop.

Target Market(s)

Commercial Property Managers - 20 to 50 year old professionals

Industry/Entity Type

Business

Requirements
Must have
• Must utilize our logo obviously, but are definitely open to using variations on the logo. Utilizing the components of the logo, but maybe in different configurations or backgrounds, etc...

Must use the Name: KORVANEX.
Can also use KORVANEX PROPERTY SERVICES.

Must include the Mission Statement

Must say: Where Care Finds Its Pulse
Nice to have
• We are considering plastic stock, shaped cards, or folding cards.

Nothing over the top or really expensive, but will consider if it conveys innovation and technology.
Should not have
• No images of toilets, buildings, trees, or anything relating to commercial properties.

We want to convey our technology image.

```html
<!DOCTYPE html>
<html lang="en">
<head>
<meta charset="utf-8">
<title>KORVANEX Business Card Set</title>
<link rel="stylesheet" href="https://fonts.googleapis.com/css2?family=Arimo:wght@700&family=PT+Sans:wght@400;700&family=Saira:wght@400;800&display=swap">
<style>
  :root {
    --brand-blue: #0f507e;
    --brand-blue-deep: #0b4470;
    --card-white: #ffffff;
    --stage-dark: #1c1c1e;
    --label-red: #e3211c;
    --text-dark: #2a2a2a;
    --swirl-tint: #cfdbe6;
    --swirl-soft: #eef3f7;
    --band-line: #9fb6c9;
  }
  * { box-sizing: border-box; margin: 0; padding: 0; }
  html, body {
    width: 1200px; height: 810px; overflow: hidden;
    background: var(--stage-dark);
  }
  .sheet { position: relative; width: 1200px; height: 810px; }

  .view-label {
    position: absolute; width: 543px; text-align: center;
    font-family: "Arimo", Arial, sans-serif; font-weight: 700;
    font-size: 34px; letter-spacing: 5px; color: var(--label-red);
  }
  .label-inner-top { left: 52px; top: 22px; }
  .label-front { left: 623px; top: 22px; }
  .label-inner-bottom { left: 52px; top: 732px; }
  .label-back { left: 623px; top: 732px; }

  .card {
    position: absolute; width: 543px; height: 308px;
    background: var(--card-white); border-radius: 24px; overflow: hidden;
  }
  .card-inner-top { left: 52px; top: 80px; }
  .card-front { left: 623px; top: 80px; }
  .card-inner-bottom { left: 52px; top: 407px; }
  .card-back { left: 623px; top: 407px; }

  .brand-mark { background: var(--brand-blue); border-radius: 10px; margin: 0 auto; }
  .brand-name {
    font-family: "Saira", sans-serif; font-weight: 800; color: var(--brand-blue);
    text-align: center; letter-spacing: 2px; line-height: 1;
  }

  /* Inner top */
  .card-inner-top .brand-mark { width: 116px; height: 116px; margin-top: 42px; }
  .card-inner-top .brand-name { font-size: 46px; margin-top: 22px; }
  .card-inner-top .web-line {
    position: absolute; left: 0; right: 0; bottom: 16px; text-align: center;
    font-family: "Saira", sans-serif; font-size: 19px; letter-spacing: 3px; color: var(--text-dark);
  }

  /* Front */
  .card-front .brand-mark { width: 74px; height: 74px; margin-top: 22px; }
  .card-front .brand-name { font-size: 25px; margin-top: 16px; }
  .contact-band {
    position: absolute; left: 0; right: 0; top: 168px; height: 91px;
    background: var(--brand-blue);
    border-top: 2px solid var(--band-line); border-bottom: 2px solid var(--band-line);
    font-family: "Saira", sans-serif; font-size: 15px; color: var(--card-white); line-height: 20px;
  }
  .address-block { position: absolute; right: 266px; top: 13px; text-align: right; }
  .band-divider { position: absolute; left: 287px; top: 30px; width: 1px; height: 28px; background: var(--band-line); }
  .contact-list { position: absolute; left: 298px; top: 10px; list-style: none; }
  .contact-list li { display: flex; align-items: center; gap: 6px; }
  .contact-list svg { width: 11px; height: 11px; fill: none; stroke: var(--card-white); stroke-width: 1.6; }
  .holder-line {
    position: absolute; left: 0; right: 0; top: 266px; text-align: center;
    font-family: "PT Sans", sans-serif; font-size: 21px; color: var(--brand-blue);
  }
  .holder-line .holder-title { font-size: 14px; color: var(--text-dark); }

  /* Inner bottom */
  .faint-swirl {
    position: absolute; inset: 0;
    background: radial-gradient(ellipse 60% 70% at 42% 48%, var(--swirl-soft) 0%, var(--swirl-soft) 45%, var(--card-white) 80%);
  }
  .mission-text {
    position: absolute; left: 40px; right: 40px; top: 62px; text-align: center;
    font-family: "PT Sans", sans-serif; font-size: 16.5px; line-height: 29.5px; color: var(--brand-blue);
  }

  /* Back */
  .swirl-pattern {
    position: absolute; inset: 0;
    background: linear-gradient(180deg, var(--swirl-soft) 0%, #e3ebf2 50%, var(--swirl-soft) 100%);
  }
  .card-back .brand-name {
    position: absolute; left: 0; right: 0; top: 126px; font-size: 60px; letter-spacing: 4px;
  }
  .tagline {
    position: absolute; left: 0; right: 0; top: 244px; text-align: center;
    font-family: "PT Sans", sans-serif; font-weight: 700; font-size: 25px; color: var(--brand-blue-deep);
  }
</style>
</head>
<body>
<main class="sheet">
  <div class="view-label label-inner-top">Inner Top</div>
  <div class="view-label label-front">Front</div>

  <section class="card card-inner-top">
    <div class="brand-mark"></div>
    <div class="brand-name">KORVANEX</div>
    <div class="web-line">www.korvanex-demo.net</div>
  </section>

  <section class="card card-front">
    <div class="brand-mark"></div>
    <div class="brand-name">KORVANEX</div>
    <div class="contact-band">
      <div class="address-block">1250 Meridian Ridge Way<br>Suite 400<br>San Diego, CA 92199</div>
      <div class="band-divider"></div>
      <ul class="contact-list">
        <li><svg viewBox="0 0 12 12"><path d="M2 1.5l2 0 1 2.5-1.2 1a6 6 0 0 0 3.2 3.2l1-1.2 2.5 1v2a1 1 0 0 1-1 1A9 9 0 0 1 1 2.5a1 1 0 0 1 1-1z"/></svg>1(866) 555-0142</li>
        <li><svg viewBox="0 0 12 12"><rect x="1" y="2.5" width="10" height="7"/><path d="M1 2.5l5 4 5-4"/></svg>info@korvanex-demo.net</li>
        <li><svg viewBox="0 0 12 12"><circle cx="6" cy="6" r="5"/><ellipse cx="6" cy="6" rx="2.2" ry="5"/><path d="M1 6h10"/></svg>www.korvanex-demo.net</li>
      </ul>
    </div>
    <div class="holder-line">Your Name, <span class="holder-title">Title</span></div>
  </section>

  <section class="card card-inner-bottom">
    <div class="faint-swirl" role="img" aria-label="Faint pale blue swirl decoration behind the mission statement"></div>
    <p class="mission-text">Korvanex is The Leading Building Services Innovator.<br>By Combining Technology With Functional Toos That<br>Improve Efficiency In The Workplace, We Provide<br>Unparalleled Service in The Industry. Developing<br>Lasting Relationships With Our Clients and Associates<br>is The Cornerstone of Our Success.</p>
  </section>

  <section class="card card-back">
    <div class="swirl-pattern" role="img" aria-label="Repeating pale blue swirl pattern background"></div>
    <div class="brand-name">KORVANEX</div>
    <div class="tagline">Where Care Finds Its Pulse</div>
  </section>

  <div class="view-label label-inner-bottom">Inner Bottom</div>
  <div class="view-label label-back">Back</div>
</main>
</body>
</html>
```